Im want a website LIKE VRX's and FleetHollow.com's with product payment options like Trenzo's

I need a website LIKE VRX with a header made EXACTLY LIKE THAT OF FLEETHOLLOWS .

The front page photo should be like that of FLEETHOLLOW's webpage as well.

The name of the website will be called "M.K. (Caldera Key)".

We will be targeting ALL MARKETS in a small town in central Panama and charging businesses "listing fees" like a phone book does but also providing informational blogs, news, and other interesting activities.

THIS IS A MULTI PAGE WEBSITE

THIS IS WHERE VRX's website meets Brivelle/FleetHollow.

Once the layout is built I will tweak and modify, add information, and upload items for sale.

Here is a list of specific categories that should be listed out above the front page header image/search bar

-- Home -- News -- Travel -- Activities -- Shop & Dine -- Store -- More... --

These categories should be spread across the bottom of the page in three sections:

WHATS SO GREAT ABOUT (Caldera Key),
HAND PICKED TOURS
ACTIVITIES etc.

Also lets use www.Trenzo.example 's
"HOT DESTINATIONS"
"BEAT THE BEST PRICES IN BOQUETE"
"OCTOBERS INSIDER PICKS"
"TOP DESTINATIONS"
and spread them in four sections side-by-side near the bottom of the page.

Overall I would like to see the finished product to be something LIKE VRX's and FleetHollows.

WE NEED ONLINE PAYMENT OPTIONS LIKE BRIVELLE'S WEBSITE HAS

This will be a desktop website but should be very mobile friendly as well.

-rodmund

P.S. Good luck!

If it isn't already too late to change the website name, the name of the website should be "Caldera Key". Added Friday, October 9, 2015

What do you guys think the budget should be to win this? Added Saturday, October 10, 2015

www.palmorra.example is the most amazing simple site. Whoever can make me a replica with my specifications will win immediately!!!! Added Sunday, October 18, 2015

OMG www.palmorra.example is the bomb!So simple and elegant. Whoever can make me an EXACT REPLICA OF WWW.PALMORRA.EXAMPLE as my site with the specifications mentioned in my brief will take home the $825.00 immediately! Good luck amigos! Added Sunday, October 18, 2015

Does anybody know how to add recurring monthly billing options on this website? Added Sunday, October 18, 2015

ALL MARKETS

Product

Coded - Design and coding required

5+ page

• Coinvey payment options.
• I must be able to add and remove photos/text and video from the HTML files in the page.
• Be creative my friends, and may the odds be forever in your favor!
• I added some photos of a good layout for our page below.

```html
<!DOCTYPE html>
<html lang="en">
<head>
<meta charset="utf-8">
<title>Caldera Key — Travel</title>
<link href="https://fonts.googleapis.com/css2?family=Roboto:wght@300;400;500;700&display=swap" rel="stylesheet">
<style>
:root{
  --teal:#1fa5a0;
  --teal-dark:#178a86;
  --ink:#2b2b2b;
  --muted:#8a8a8a;
  --line:#e4e4e4;
  --topbar:#111416;
  --footer:#1b1d1f;
  --footer-low:#141517;
  --star:#1fa5a0;
  --bg:#ffffff;
  --field:#f4f4f4;
}
*{box-sizing:border-box;margin:0;padding:0}
html,body{width:682px;height:1200px;overflow:hidden;background:var(--bg)}
body{font-family:'Roboto',Arial,sans-serif;color:var(--ink);font-size:8px;position:relative}
.wrap{padding:0 36px}

/* top bar */
.topbar{height:27px;background:var(--topbar);display:flex;align-items:center;justify-content:space-between;padding:0 36px;color:#ccc;font-size:6px}
.brand{color:var(--teal);font-size:13px;font-weight:500}
.top-search{width:150px;height:13px;background:#fff;border-radius:2px;display:flex;justify-content:flex-end;align-items:center;padding-right:4px}
.top-links{display:flex;gap:10px;letter-spacing:.3px}

/* nav */
.mainnav{height:23px;background:var(--teal);display:flex;padding:0 36px;align-items:stretch}
.mainnav a{color:#fff;text-decoration:none;font-size:6.5px;font-weight:500;padding:0 10px;display:flex;align-items:center;letter-spacing:.4px}
.mainnav a.active{background:var(--teal-dark)}

/* hero */
.hero{position:relative;height:300px;background:linear-gradient(180deg,#4a4e50 0%,#6c6f70 35%,#5a5d5e 70%,#2f3132 100%)}
.hero-photo{position:absolute;inset:0;background:radial-gradient(ellipse at 50% 45%,#9a9c9c 0%,rgba(90,93,94,0) 45%),linear-gradient(90deg,#2a2c2d 0%,rgba(0,0,0,0) 30%,rgba(0,0,0,0) 70%,#2a2c2d 100%)}
.hero-title{position:absolute;top:85px;width:100%;text-align:center;color:#fff;font-weight:300;font-size:54px;letter-spacing:3px}
.hero-from{position:absolute;top:150px;width:100%;text-align:center;color:#fff;font-size:7px}
.hero-price{position:absolute;top:160px;width:100%;text-align:center;color:var(--teal);font-size:20px;font-weight:300}
.hero-arrow{position:absolute;top:140px;width:16px;height:16px;border-radius:50%;background:rgba(255,255,255,.25);display:flex;align-items:center;justify-content:center}
.hero-arrow.left{left:12px}.hero-arrow.right{right:12px}
.tabs{position:absolute;bottom:0;left:36px;display:flex;height:20px}
.tabs span{background:rgba(20,22,24,.85);color:#ddd;font-size:6px;padding:0 12px;display:flex;align-items:center;gap:4px;letter-spacing:.3px}
.tabs span.active{background:var(--teal);color:#fff}
.tabs i{width:5px;height:5px;background:currentColor;border-radius:1px;display:inline-block}

/* search */
.search-card{margin:0 36px;padding:14px 14px 16px;border-bottom:1px solid var(--line)}
.search-card h2{font-size:19px;font-weight:300;margin-bottom:8px}
.search-row{display:flex;gap:8px;align-items:flex-end}
.field label{display:block;font-size:6px;color:#555;margin-bottom:3px}
.input{height:18px;border:1px solid var(--line);background:var(--field);font-size:5.5px;color:var(--muted);display:flex;align-items:center;padding:0 5px;gap:4px}
.f-where{width:170px}.f-date{width:72px}
.counter{display:flex;gap:6px;align-items:center;font-size:6px;color:#555;height:18px}
.counter b{width:13px;height:13px;border-radius:50%;background:var(--teal);color:#fff;display:flex;align-items:center;justify-content:center;font-weight:500}
.btn{display:inline-block;margin-top:10px;background:var(--teal);color:#fff;font-size:6.5px;padding:6px 10px;border-radius:1px}

/* deals */
.deals{display:flex;gap:22px;padding:16px 36px 0}
.deal-col{flex:1}
.deal-col h3{font-size:13px;font-weight:400;margin-bottom:8px}
.deal-col h3 small{font-size:5px;color:var(--teal);margin-left:4px}
.deal{display:flex;align-items:center;gap:7px;border:1px solid var(--line);padding:5px;margin-bottom:7px;height:42px}
.thumb{width:50px;height:32px;flex:none}
.t1{background:linear-gradient(135deg,#6b5a48,#c9b49a)}
.t2{background:linear-gradient(135deg,#3e5b6e,#a9c1cf)}
.t3{background:linear-gradient(135deg,#55483d,#b49878)}
.deal-info{flex:1}
.deal-info p{font-size:5.5px;color:#444;margin-bottom:3px}
.stars{color:var(--star);font-size:6px;letter-spacing:.5px}
.price{text-align:right}
.price small{display:block;font-size:4.5px;color:var(--muted)}
.price strong{font-size:9px;font-weight:500}

/* destinations */
.destinations{padding:30px 36px 0}
.destinations h2{font-size:22px;font-weight:300;margin-bottom:14px}
.dest-row{display:flex;gap:22px}
.dest{flex:1}
.dest-img{height:110px}
.d-greece{background:linear-gradient(180deg,#6fa8d8 0%,#9fcbe6 45%,#47b3b8 60%,#e8ddc6 80%,#d9cdb3 100%)}
.d-africa{background:linear-gradient(180deg,#3a2418 0%,#a8481e 40%,#f0b040 55%,#7a3418 75%,#2a1810 100%)}
.d-australia{background:linear-gradient(180deg,#9aa6b2 0%,#c0c4c4 45%,#6e7f8a 70%,#4f5a60 100%)}
.dest h4{font-size:8px;font-weight:400;margin:7px 0 3px}
.dest p{font-size:5px;color:var(--muted);line-height:1.4}

/* footer */
.footer{position:absolute;top:1010px;left:0;width:682px;height:190px;background:var(--footer);color:#bbb}
.foot-cols{display:flex;padding:26px 36px 0;gap:20px}
.foot-brand{width:150px}
.foot-brand .brand{display:block;margin-bottom:8px}
.foot-brand p{font-size:5.5px;line-height:1.5;color:#999}
.social{display:flex;gap:4px;margin-top:10px}
.social span{width:11px;height:11px;border-radius:50%;background:var(--teal)}
.foot-news{width:130px}
.foot-news h5,.foot-help h5{color:#fff;font-size:11px;font-weight:400;margin-bottom:6px}
.foot-news p{font-size:5.5px;color:#999;margin-bottom:5px}
.news-input{height:14px;background:#2c2f31;margin-bottom:6px}
.news-btn{display:inline-block;background:var(--teal);color:#fff;font-size:5.5px;padding:4px 8px}
.foot-links{width:110px;list-style:none;font-size:5.5px;line-height:1.9;color:#aaa}
.foot-help{flex:1}
.foot-help .phone{color:var(--teal);font-size:10px;margin-bottom:3px}
.foot-help p{font-size:5.5px;color:#999;line-height:1.6}
.foot-bottom{position:absolute;bottom:0;left:0;width:100%;height:20px;background:var(--footer-low)}
</style>
</head>
<body>

<header class="topbar">
  <span class="brand">Caldera Key</span>
  <div class="top-search">
    <svg width="6" height="6" viewBox="0 0 10 10"><circle cx="4" cy="4" r="3" fill="none" stroke="#555" stroke-width="1.4"/><line x1="6.3" y1="6.3" x2="9" y2="9" stroke="#555" stroke-width="1.4"/></svg>
  </div>
  <nav class="top-links"><span>Sign in</span><span>SIGN IN</span><span>$ USD</span></nav>
</header>

<nav class="mainnav">
  <a class="active">HOME ▾</a><a>PAGES ▾</a><a>FEATURES ▾</a><a>HOTELS ▾</a><a>FLIGHTS ▾</a><a>RENTALS ▾</a><a>CARS ▾</a><a>ACTIVITIES ▾</a>
</nav>

<section class="hero">
  <div class="hero-photo" role="img" aria-label="Photo of Paris with the Eiffel Tower seen between tall buildings"></div>
  <div class="hero-title">PARIS</div>
  <div class="hero-from">from</div>
  <div class="hero-price">$400</div>
  <div class="hero-arrow left"><svg width="6" height="6" viewBox="0 0 10 10"><path d="M7 1 3 5l4 4" fill="none" stroke="#fff" stroke-width="1.5"/></svg></div>
  <div class="hero-arrow right"><svg width="6" height="6" viewBox="0 0 10 10"><path d="M3 1l4 4-4 4" fill="none" stroke="#fff" stroke-width="1.5"/></svg></div>
  <div class="tabs">
    <span class="active"><i></i>HOTELS</span><span><i></i>FLIGHTS</span><span><i></i>RENTALS</span><span><i></i>CARS</span><span><i></i>ACTIVITIES</span>
  </div>
</section>

<section class="search-card">
  <h2>Search and Save on Hotels</h2>
  <div class="search-row">
    <div class="field"><label>Where are you going?</label><div class="input f-where">
      <svg width="5" height="6" viewBox="0 0 10 12"><path d="M5 0a4 4 0 0 1 4 4c0 3-4 8-4 8S1 7 1 4a4 4 0 0 1 4-4z" fill="#aaa"/></svg>City, airport, region, landmark or address</div></div>
    <div class="field"><label>Check in</label><div class="input f-date">Sep 12, Mon</div></div>
    <div class="field"><label>Check out</label><div class="input f-date">Sep 14, Wed</div></div>
    <div class="field"><label>Rooms</label><div class="counter"><b>1</b>2 3 3+</div></div>
    <div class="field"><label>Guests</label><div class="counter"><b>1</b>2 3 3+</div></div>
  </div>
  <span class="btn">Search for Hotels</span>
</section>

<section class="deals">
  <div class="deal-col">
    <h3>Trendy Now<small>view all</small></h3>
    <div class="deal"><div class="thumb t1" role="img" aria-label="Hotel room photo"></div><div class="deal-info"><p>The Harbor Inn</p><div class="stars">★★★★★</div></div><div class="price"><small>From</small><strong>$230</strong></div></div>
    <div class="deal"><div class="thumb t2" role="img" aria-label="Hotel pool photo"></div><div class="deal-info"><p>The Bay Suites</p><div class="stars">★★★★★</div></div><div class="price"><small>From</small><strong>$257</strong></div></div>
    <div class="deal"><div class="thumb t3" role="img" aria-label="Hotel lobby photo"></div><div class="deal-info"><p>Hillside Lodge Hotel</p><div class="stars">★★★★★</div></div><div class="price"><small>From</small><strong>$322</strong></div></div>
  </div>
  <div class="deal-col">
    <h3>Hot Deals<small>view all</small></h3>
    <div class="deal"><div class="thumb t3" role="img" aria-label="Hotel suite photo"></div><div class="deal-info"><p>River Park Hotel</p><div class="stars">★★★★★</div></div><div class="price"><small>From</small><strong>$480</strong></div></div>
    <div class="deal"><div class="thumb t1" role="img" aria-label="Hotel bedroom photo"></div><div class="deal-info"><p>The Cedar House</p><div class="stars">★★★★★</div></div><div class="price"><small>From</small><strong>$186</strong></div></div>
    <div class="deal"><div class="thumb t2" role="img" aria-label="Hotel terrace photo"></div><div class="deal-info"><p>Garden Suites</p><div class="stars">★★★★★</div></div><div class="price"><small>From</small><strong>$278</strong></div></div>
  </div>
  <div class="deal-col">
    <h3>Special for You<small>view all</small></h3>
    <div class="deal"><div class="thumb t2" role="img" aria-label="Hotel exterior photo"></div><div class="deal-info"><p>The Valley Inn</p><div class="stars">★★★★★</div></div><div class="price"><small>From</small><strong>$182</strong></div></div>
    <div class="deal"><div class="thumb t1" role="img" aria-label="Hotel room photo"></div><div class="deal-info"><p>The Coral Hotel</p><div class="stars">★★★★★</div></div><div class="price"><small>From</small><strong>$245</strong></div></div>
    <div class="deal"><div class="thumb t3" role="img" aria-label="Hotel dining room photo"></div><div class="deal-info"><p>The Palm Resort</p><div class="stars">★★★★★</div></div><div class="price"><small>From</small><strong>$234</strong></div></div>
  </div>
</section>

<section class="destinations">
  <h2>Explore Our Top Destinations</h2>
  <div class="dest-row">
    <div class="dest"><div class="dest-img d-greece" role="img" aria-label="Photo of a white sand beach with turquoise water in Greece"></div><h4>Greece</h4><p>Sunny islands, calm bays and old towns to discover.</p></div>
    <div class="dest"><div class="dest-img d-africa" role="img" aria-label="Photo of an orange sunset over the African savanna"></div><h4>Africa</h4><p>Wide plains, golden sunsets and wildlife safaris.</p></div>
    <div class="dest"><div class="dest-img d-australia" role="img" aria-label="Photo of a quiet Australian coastline under grey sky"></div><h4>Australia</h4><p>Long coasts, open skies and lively harbor cities.</p></div>
  </div>
</section>

<footer class="footer">
  <div class="foot-cols">
    <div class="foot-brand">
      <span class="brand">Caldera Key</span>
      <p>Booking, reliable and secure on hotels, tours, flights, vacation rentals, travel packages and more deals.</p>
      <div class="social"><span></span><span></span><span></span><span></span><span></span><span></span></div>
    </div>
    <div class="foot-news">
      <h5>Newsletter</h5>
      <p>Enter your E-mail Address</p>
      <div class="news-input"></div>
      <span class="news-btn">Subscribe</span>
    </div>
    <ul class="foot-links">
      <li>About Us</li><li>Press Centre</li><li>Best Price Guarantee</li><li>Travel News</li><li>Jobs</li><li>Privacy Policy</li><li>Terms of Use</li><li>Feedback</li>
    </ul>
    <div class="foot-help">
      <h5>Have Questions?</h5>
      <div class="phone">+1 000-555-0142</div>
      <p>hello@calderakey.example</p>
      <p>24/7 Dedicated Customer Support</p>
    </div>
  </div>
  <div class="foot-bottom"></div>
</footer>

</body>
</html>
```